Business cards in digital learning for freelancer

Hello, I need a business cards in french. I work in the Digital learning industries as freeelancer; I'm an expert in digital learning. I work in France. My customer are in the health industry, pharmaceutical industry, and training organization. I've got a logo. I offer three services: consulting, Design, and Training. In the consulting, I offers coaching to choose your digital learning tools and the digital learning strategy. For the Design, I product differents level of elearning like rapid-learning, elearning, micro-learning, video-learning. And for the training service, I've create training about pedagogy, digital learning management project, Digital learning design.
I join my Logo create in this platform. My universe is gamified. I like the life, and I'm very social. I want a card like I'm I. I love Art (painting), Europeen comics. I use in my visual support "permanent maker" font and caracters. I would like cards: elegant, modern, Top class. If you need any information, you can ask me.
thanks for ideas

Target Market(s)

in health industries and training organization for Training manager, instructor, human resources director

Contact Information for Business Card

Phone number : 06 71 38 95 14 , mail: bastiengolmier@quelmoto.fr, web: bastiengolmier.fr , Carrivo

Font styles to use
Sans Serif

Requirements
Must have
• Use my logo and write my 3 services (consulting, training, design)

```html
<!DOCTYPE html>
<html lang="fr">
<head>
<meta charset="utf-8">
<title>Golmier Digital Learning – Cartes de visite</title>
<link rel="stylesheet" href="https://fonts.googleapis.com/css2?family=Arimo:wght@400;700&family=Cinzel:wght@400;600&family=Cormorant+Garamond:wght@500&display=swap">
<style>
  :root {
    --bg: #2b2b2d;
    --card-front: #ffffff;
    --card-back: #1c1d1f;
    --pattern: #242528;
    --orange: #f26f21;
    --grey: #6d6e71;
    --grey-dark: #4a4a4c;
    --rule: #8a8b8d;
  }
  * { margin: 0; padding: 0; box-sizing: border-box; }
  html, body {
    width: 1200px; height: 1108px; overflow: hidden;
    background: var(--bg);
  }
  .canvas {
    width: 1200px; height: 1108px;
    display: flex; align-items: center; justify-content: center; gap: 80px;
  }
  .card {
    width: 420px; height: 650px;
    border-radius: 22px;
    position: relative;
    overflow: hidden;
  }
  /* Front */
  .card--front {
    background: var(--card-front);
    display: flex; flex-direction: column; align-items: center;
    padding-top: 120px;
    font-family: "Arimo", Arial, sans-serif;
  }
  .brand { display: flex; align-items: center; gap: 14px; }
  .brand__dot { width: 30px; height: 30px; border-radius: 50%; background: var(--orange); }
  .brand__name {
    font-family: "Arimo", Arial, sans-serif; font-weight: 700;
    font-size: 56px; letter-spacing: 2px; color: var(--orange); line-height: 1;
  }
  .tagline {
    display: flex; align-items: center; gap: 10px; margin-top: 10px;
    font-family: "Cormorant Garamond", Georgia, serif;
    font-size: 17px; letter-spacing: 2px; color: var(--grey);
  }
  .tagline::before, .tagline::after {
    content: ""; width: 60px; height: 1.5px; background: var(--rule);
  }
  .services {
    margin-top: 22px;
    font-size: 17px; color: var(--grey-dark); letter-spacing: .5px;
    display: flex; align-items: center; gap: 9px;
  }
  .services__sep { width: 9px; height: 9px; border-radius: 50%; background: var(--orange); }
  .person { margin-top: 66px; text-align: center; }
  .person__name {
    font-family: "Cinzel", Georgia, serif; font-weight: 400;
    font-size: 28px; color: var(--orange); letter-spacing: 1px;
  }
  .person__role { font-size: 19px; color: var(--grey-dark); margin-top: 2px; }
  .contact-icons {
    margin-top: 18px; display: flex; align-items: center; gap: 6px;
  }
  .contact-icons::before, .contact-icons::after {
    content: ""; width: 70px; height: 1px; background: var(--rule); margin: 0 8px;
  }
  .icon {
    width: 34px; height: 34px; border-radius: 5px; background: var(--orange);
    display: flex; align-items: center; justify-content: center;
  }
  .contact-list {
    list-style: none; text-align: center; margin-top: 12px;
    font-size: 19px; color: var(--grey-dark); line-height: 1.3;
  }
  .network {
    margin-top: 20px; display: flex; align-items: center; gap: 10px;
    font-size: 16px; color: var(--orange); font-weight: 700;
  }
  .network::before, .network::after {
    content: ""; width: 100px; height: 1px; background: var(--rule);
  }
  .network__dot { width: 12px; height: 12px; border-radius: 50%; background: var(--orange); }
  /* Back */
  .card--back {
    background: var(--card-back);
    display: flex; align-items: center; justify-content: center;
  }
  .back-pattern {
    position: absolute; inset: 0;
    background: linear-gradient(160deg, var(--pattern) 0%, var(--card-back) 75%);
  }
  .back-mark {
    position: relative; display: flex; align-items: center; gap: 8px;
    margin-top: 330px;
  }
  .back-mark__dot { width: 14px; height: 14px; border-radius: 50%; background: var(--orange); }
  .back-mark__name {
    font-family: "Arimo", Arial, sans-serif; font-weight: 700;
    font-size: 22px; letter-spacing: 1px; color: var(--orange);
  }
</style>
</head>
<body>
<main class="canvas">
  <section class="card card--front">
    <div class="brand">
      <span class="brand__dot"></span>
      <span class="brand__name">GOLMIER</span>
    </div>
    <p class="tagline">DIGITAL LEARNING</p>
    <p class="services">
      <span>CONSULTING</span><span class="services__sep"></span>
      <span>TRAINING</span><span class="services__sep"></span>
      <span>DESIGN</span>
    </p>
    <div class="person">
      <h1 class="person__name">BASTIEN GOLMIER</h1>
      <p class="person__role">Managing Director</p>
    </div>
    <div class="contact-icons">
      <span class="icon" aria-label="Téléphone">
        <svg width="20" height="20" viewBox="0 0 24 24"><path fill="#fff" d="M6.6 10.8a15 15 0 0 0 6.6 6.6l2.2-2.2a1 1 0 0 1 1-.25 11.4 11.4 0 0 0 3.6.57 1 1 0 0 1 1 1V20a1 1 0 0 1-1 1A17 17 0 0 1 3 4a1 1 0 0 1 1-1h3.5a1 1 0 0 1 1 1c0 1.25.2 2.45.57 3.57a1 1 0 0 1-.25 1z"/></svg>
      </span>
      <span class="icon" aria-label="E-mail">
        <svg width="20" height="20" viewBox="0 0 24 24"><rect x="3" y="5" width="18" height="14" rx="1" fill="none" stroke="#fff" stroke-width="2"/><path d="M3 6l9 7 9-7" fill="none" stroke="#fff" stroke-width="2"/></svg>
      </span>
      <span class="icon" aria-label="Site web">
        <svg width="20" height="20" viewBox="0 0 24 24" fill="none" stroke="#fff" stroke-width="1.8"><circle cx="12" cy="12" r="9"/><path d="M3 12h18M12 3c3 3 3 15 0 18M12 3c-3 3-3 15 0 18"/></svg>
      </span>
    </div>
    <ul class="contact-list">
      <li>06 71 38 95 14</li>
      <li>bastiengolmier@quelmoto.fr</li>
      <li>www.bastiengolmier.fr</li>
    </ul>
    <p class="network"><span class="network__dot"></span>Carrivo</p>
  </section>

  <section class="card card--back">
    <div class="back-pattern" role="img" aria-label="Motif discret répétant l'emblème de la marque sur fond sombre"></div>
    <div class="back-mark">
      <span class="back-mark__dot"></span>
      <span class="back-mark__name">GOLMIER</span>
    </div>
  </section>
</main>
</body>
</html>
```